Design and Renovation Company Luxury Business Card

I want to create a luxury business card for a Design and Renovation Firm . We will use our current logo. The company name is 528BUILDA. We do not want anything standard. We need a very unique concept.
Please see uploaded inspiration. I really like the textured paper option. I would like the card to be thick with debossing, and/or embossing options. The logo has orange in it but I would like to see the card with and without the orange. I think the orange may make the company feel less high-end. The goal is to elevate the logo not match its vibe per se of the logo. We want something very unique, not standard at all!
I would like a space for :
Logo,
Name,
Position,
Email,
Office number,
Website Address,
Business Address,
Thank you!
Have fun!
Target Market(s)
Home owners Age 35 +
Industry/Entity Type
Design and Renovation
Contact Information for Business Card
Logo, Name, Position, Email, Office number, Website Address, Business Address,.
Colors
Designer to choose colors to be used in the design.
Requirements
Must have
- A luxury designer feel. Must be black or dark grey but open to other luxury ideas.
Nice to have
- Gold, silver, black embossing or debossing. Textured paper design.
Should not have
- A cheap look and feel.

```html
<!DOCTYPE html>
<html lang="en">
<head>
<meta charset="utf-8">
<title>528BUILDA Business Card</title>
<link rel="stylesheet" href="https://fonts.googleapis.com/css2?family=Montserrat:wght@400;500;700&display=swap">
<style>
  :root {
    --stage: #2a2a2a;
    --card: #1a1a1a;
    --card-deep: #111111;
    --accent: #f0901e;
    --ink: #f2f2f2;
    --muted: #cfcfcf;
  }
  * { box-sizing: border-box; margin: 0; padding: 0; }
  html, body { width: 1200px; height: 801px; overflow: hidden; }
  body {
    background: var(--stage);
    font-family: "Montserrat", sans-serif;
    color: var(--ink);
    position: relative;
  }
  .card {
    position: absolute;
    top: 246px;
    width: 540px;
    height: 309px;
    border-radius: 18px;
    background: var(--card);
    border-bottom: 4px solid var(--accent);
    box-shadow: 0 18px 40px rgba(0,0,0,.55);
    overflow: hidden;
  }
  .card--front { left: 45px; }
  .card--back { left: 615px; }

  .brand { position: absolute; }
  .brand__name {
    font-weight: 500;
    letter-spacing: 0;
    color: var(--ink);
    line-height: 1.1;
    white-space: nowrap;
  }
  .brand__tagline {
    font-size: 8px; letter-spacing: 1.4px; color: var(--muted); margin-top: 5px;
    white-space: nowrap;
  }
  .card--front .brand { left: 34px; top: 110px; }
  .card--front .brand__name { font-size: 30px; }

  .person { position: absolute; right: 34px; top: 30px; text-align: right; }
  .person__name { color: var(--accent); font-weight: 700; font-size: 19px; }
  .person__role { font-size: 10px; color: var(--muted); margin-top: 2px; }

  .feature-tiles {
    position: absolute; right: 34px; top: 96px; width: 150px; height: 130px;
    border-radius: 4px;
    background: linear-gradient(160deg, #4a4a4a 0%, #232323 55%, #0a0a0a 100%);
  }

  .contact { position: absolute; left: 34px; bottom: 26px; font-size: 10.5px; line-height: 1.55; }
  .contact__address { margin-bottom: 10px; color: var(--ink); }
  .contact__row { display: flex; align-items: center; gap: 8px; }
  .contact__icon { width: 11px; height: 11px; flex: none; }

  .tile-field {
    position: absolute; inset: 0;
    background: linear-gradient(200deg, #3c3c3c 0%, #222 45%, var(--card-deep) 100%);
  }
  .card--back .brand { right: 40px; bottom: 62px; text-align: left; }
  .card--back .brand__name { font-size: 40px; }
  .card--back .brand__tagline { font-size: 10px; }
</style>
</head>
<body>
  <section class="card card--front">
    <div class="person">
      <p class="person__name">Daniel Hayes</p>
      <p class="person__role">Managing Director</p>
    </div>

    <div class="brand">
      <p class="brand__name">528BUILDA</p>
      <p class="brand__tagline">Design and Renovation Firm</p>
    </div>

    <div class="feature-tiles" role="img" aria-label="Large glossy tile decoration"></div>

    <div class="contact">
      <p class="contact__address">415 Linden Park Ave, #112<br>Brookfield, OH 430140</p>
      <p class="contact__row">
        <svg class="contact__icon" viewBox="0 0 12 12" aria-hidden="true"><path d="M2.5 1h2l1 3-1.3 1a6 6 0 0 0 2.8 2.8l1-1.3 3 1v2a1 1 0 0 1-1 1A9.5 9.5 0 0 1 1.5 2a1 1 0 0 1 1-1z" fill="#f0901e"/></svg>
        555-318-0472
      </p>
      <p class="contact__row">
        <svg class="contact__icon" viewBox="0 0 12 12" aria-hidden="true"><rect x="0.5" y="2.5" width="11" height="7.5" rx="1" fill="#f0901e"/><path d="M1 3l5 4 5-4" stroke="#1a1a1a" stroke-width="1" fill="none"/></svg>
        info@studiodomain.com
      </p>
      <p class="contact__row">
        <svg class="contact__icon" viewBox="0 0 12 12" aria-hidden="true"><circle cx="6" cy="6" r="5" fill="none" stroke="#f0901e" stroke-width="1.3"/><path d="M1 6h10M6 1c-2.4 2.8-2.4 7.2 0 10M6 1c2.4 2.8 2.4 7.2 0 10" stroke="#f0901e" stroke-width="1" fill="none"/></svg>
        www.studiodomain.com
      </p>
    </div>
  </section>

  <section class="card card--back">
    <div class="tile-field" role="img" aria-label="Scattered glossy square tile pattern fading from grey to black"></div>
    <div class="brand">
      <p class="brand__name">528BUILDA</p>
      <p class="brand__tagline">Design and Renovation Firm</p>
    </div>
  </section>
</body>
</html>
```